Luxury Wine Label for New Startup Winery

We need a wine label for our new winery startup. We have worked with a local designer but do not feel the resulting label / logo have the elevation required to present our brand as a luxury wine. Our winery is called "Quailbrook Vineyards" and we are focused on extremely high quality hand crafted artisan and estate wines from the Pacific Northwest.
We would like to see designs that utilize a tree line, or other imagery that represents the "Quailbrook" part of our company name. Another interesting feature could be wood grain.
A logo will be required based on your design so please design with this in mind:
This logo should be consistent with the wine bottle label design, and should be representative of our high end exclusive wine while giving a sense of place (Oregon/ Pacific Northwest.)
I will supply an image of the design we received from our local designer, PLEASE NOTE: in general we do like wood grain and tree line concepts but feel the execution was poorly done.
ATTN: Logo design should be suitable for use on: Bottles (Red wine/rose/white wine), Bussiness cards, vehicle signage, business signage, etc
P.S.:
If you have a design that is not outside the box we are still interested in seeing it.
Label is for a burgundy style bottle with a label height of 3.5 - 4" and a width of 3.5-4"
any label <= 4"x4" and >=3.5"x3.5" will be acceptable:
HOWEVER Width should be greater than or equal to height due to the bottle format
Target Market(s)
Wine enthusiasts with adequate discretionary budgets to afford $100 bottles of wine.
Industry/Entity Type
Wine / Winery
Requirements
Must have
- A sense of luxury, a feel of exclusivity, and a theme consistent with our product and brand name
Nice to have
- Tree line, wood grain or other wood themes. Serif fonts
Should not have
- anything cheesy, off topic, hard to read script fonts or anything that makes the label hard to read from a few feet away or too busy

```html
<!DOCTYPE html>
<html lang="en">
<head>
<meta charset="utf-8">
<title>Quailbrook Vineyards – Syrah Label</title>
<link rel="stylesheet" href="https://fonts.googleapis.com/css2?family=Cinzel:wght@400&display=swap">
<style>
  :root {
    --backdrop: #f1f5f7;
    --label-black: #050506;
    --label-sheen: #15171b;
    --silver: #c4c5c9;
    --rule-silver: #8c8e94;
    --gold: #b8923a;
    --wood-dark: #1e120b;
    --wood-mid: #5a3519;
    --wood-warm: #7a4a22;
    --varietal-ivory: #ece7de;
  }
  html, body {
    margin: 0;
    padding: 0;
    width: 1200px;
    height: 2202px;
    overflow: hidden;
    background: var(--backdrop);
  }
  .canvas {
    position: relative;
    width: 1200px;
    height: 2202px;
    font-family: "Cinzel", "Times New Roman", serif;
  }
  .label-main {
    position: absolute;
    left: 150px;
    top: 638px;
    width: 900px;
    height: 591px;
    background: linear-gradient(90deg, var(--label-black) 0%, var(--label-sheen) 26%, var(--label-black) 40%, var(--label-black) 100%);
  }
  .rule {
    position: absolute;
    left: 0;
    width: 100%;
    height: 2px;
    background: linear-gradient(90deg, var(--rule-silver) 0%, #d8d9dc 60%, var(--rule-silver) 100%);
  }
  .rule--top { top: 81px; }
  .rule--bottom { top: 507px; }
  .brand-name {
    position: absolute;
    left: 0;
    width: 100%;
    text-align: center;
    color: var(--silver);
    font-weight: 400;
    line-height: 1;
    margin: 0;
  }
  .brand-name__primary {
    top: 298px;
    font-size: 70px;
    letter-spacing: 2px;
  }
  .brand-name__secondary {
    top: 405px;
    font-size: 50px;
    letter-spacing: 6px;
  }
  .region {
    position: absolute;
    left: 0;
    top: 540px;
    width: 100%;
    text-align: center;
    color: var(--silver);
    font-size: 20px;
    letter-spacing: 4px;
    line-height: 1;
  }
  .label-varietal {
    position: absolute;
    left: 150px;
    top: 1280px;
    width: 900px;
    height: 284px;
  }
  .wood-grain {
    position: absolute;
    inset: 0;
    background: linear-gradient(90deg, var(--wood-mid) 0%, var(--wood-warm) 18%, var(--wood-dark) 45%, var(--wood-mid) 70%, var(--wood-dark) 100%);
  }
  .gold-rule {
    position: absolute;
    left: 0;
    width: 100%;
    height: 2px;
    background: var(--gold);
  }
  .gold-rule--top { top: 45px; }
  .gold-rule--bottom { top: 236px; }
  .varietal {
    position: absolute;
    left: 0;
    top: 102px;
    width: 100%;
    text-align: center;
    color: var(--varietal-ivory);
    font-size: 78px;
    letter-spacing: 14px;
    line-height: 1;
  }
</style>
</head>
<body>
  <div class="canvas">
    <section class="label-main">
      <div class="rule rule--top"></div>
      <p class="brand-name brand-name__primary">Quailbrook</p>
      <p class="brand-name brand-name__secondary">Vineyards</p>
      <div class="rule rule--bottom"></div>
      <div class="region">WILLAMETTE VALLEY</div>
    </section>
    <section class="label-varietal">
      <div class="wood-grain" role="img" aria-label="Dark burl wood grain texture in deep browns and amber"></div>
      <div class="gold-rule gold-rule--top"></div>
      <div class="varietal">SYRAH</div>
      <div class="gold-rule gold-rule--bottom"></div>
    </section>
  </div>
</body>
</html>
```